Business card design for Automotive workshop

We need a business card for a new automotive repair and tyre shop called Keelstone Prime Automotive located in New Zealand. We are a clean, modern and fresh workshop and company.

Front needs to feature logo,
my name:
Marlo Fenwicke (director)

Address:
48 Tarn Lane
Whitianga 3510

Phone: 07 594 2713
Mobile: 027 451 9362
Email: office@keelstoneautomotive.example.nz
Website: keelstoneautomotive.example.nz

Back needs to feature an area to write down appointment details, date and time.

Also feature a list of jobs and work we do such as,
Vehicle Servicing
All Mechanical Repairs
Warrant of Fitness
Tyres & Wheel Alignments
Automotive Diagnostics
Automotive Parts & Supplies

```html
<!DOCTYPE html>
<html lang="en">
<head>
<meta charset="utf-8">
<title>Keelstone Prime Automotive – Business Card</title>
<link rel="stylesheet" href="https://fonts.googleapis.com/css2?family=Arimo:wght@400;700&family=Open+Sans:wght@400;600;800&display=swap">
<style>
  :root {
    --red: #e41e26;
    --white: #ffffff;
    --ink: #2b2b2b;
    --ink-soft: #3d3d3d;
    --rule: #c9c9c9;
    --backdrop: #e6e6e8;
  }
  * { box-sizing: border-box; margin: 0; padding: 0; }
  html, body { width: 1200px; height: 1015px; overflow: hidden; }
  body {
    background: var(--backdrop);
    font-family: "Open Sans", Arial, sans-serif;
    color: var(--ink);
    display: flex;
    flex-direction: column;
    align-items: center;
    justify-content: center;
    gap: 60px;
  }
  .card {
    width: 700px;
    height: 400px;
    position: relative;
    overflow: hidden;
    box-shadow: 0 6px 18px rgba(0,0,0,0.18);
  }

  /* Back side */
  .card-back { background: var(--red); font-family: "Arimo", Arial, sans-serif; }
  .services {
    height: 205px;
    padding: 38px 60px 0;
  }
  .services-title {
    text-align: center;
    font-weight: 700;
    font-size: 19px;
    color: var(--ink);
    letter-spacing: 0.5px;
    margin-bottom: 20px;
  }
  .service-columns {
    display: flex;
    justify-content: space-between;
    padding: 0 20px;
  }
  .service-list { list-style: none; }
  .service-list li {
    color: var(--white);
    font-size: 18px;
    line-height: 26px;
    padding-left: 18px;
    position: relative;
  }
  .service-list li::before {
    content: "";
    position: absolute;
    left: 0; top: 9px;
    width: 9px; height: 9px;
    border-radius: 50%;
    background: var(--white);
  }
  .appointment {
    background: var(--white);
    height: 150px;
    padding: 28px 70px 0;
  }
  .appointment-title {
    text-align: center;
    font-weight: 700;
    font-size: 20px;
    letter-spacing: 0.5px;
    color: var(--ink);
    margin-bottom: 38px;
  }
  .appointment-fields { display: flex; gap: 40px; }
  .field {
    flex: 1;
    display: flex;
    align-items: flex-end;
    gap: 10px;
    font-size: 19px;
    color: var(--ink);
  }
  .field-line { flex: 1; border-bottom: 1px solid var(--rule); height: 20px; }

  /* Front side */
  .card-front { background: var(--white); }
  .front-main {
    height: 300px;
    display: flex;
    align-items: center;
  }
  .brand {
    width: 330px;
    padding-left: 44px;
    font-weight: 800;
    font-size: 27px;
    line-height: 1.12;
    color: var(--red);
    text-transform: uppercase;
    letter-spacing: 0.5px;
  }
  .divider {
    width: 1px;
    height: 170px;
    background: var(--rule);
  }
  .contact { padding-left: 28px; }
  .contact-name {
    font-weight: 800;
    font-size: 22px;
    color: var(--red);
    text-transform: uppercase;
    letter-spacing: 0.3px;
  }
  .contact-role, .contact-address {
    font-size: 16px;
    color: var(--ink-soft);
    line-height: 22px;
  }
  .contact-address { margin: 6px 0 10px; }
  .contact-lines { list-style: none; }
  .contact-lines li {
    display: flex;
    align-items: center;
    gap: 8px;
    font-size: 16px;
    line-height: 23px;
    color: var(--ink-soft);
  }
  .contact-lines svg { width: 14px; height: 14px; flex: none; }
  .front-band {
    height: 100px;
    background: var(--red);
    display: flex;
    align-items: center;
    justify-content: center;
  }
  .website {
    color: var(--white);
    font-size: 25px;
    letter-spacing: 1px;
  }
</style>
</head>
<body>

  <section class="card card-back" aria-label="Card back">
    <div class="services">
      <h2 class="services-title">WORK WE DO</h2>
      <div class="service-columns">
        <ul class="service-list">
          <li>Vehicle Servicing</li>
          <li>All Mechanical Repairs</li>
          <li>Warrant of Fitness</li>
        </ul>
        <ul class="service-list">
          <li>Tyres &amp; Wheel Alignments</li>
          <li>Automotive Diagnostics</li>
          <li>Automotive Parts &amp; Supplies</li>
        </ul>
      </div>
    </div>
    <div class="appointment">
      <h2 class="appointment-title">NEXT APPOINTMENT</h2>
      <div class="appointment-fields">
        <div class="field"><span>DATE</span><span class="field-line"></span></div>
        <div class="field"><span>TIME</span><span class="field-line"></span></div>
      </div>
    </div>
  </section>

  <section class="card card-front" aria-label="Card front">
    <div class="front-main">
      <div class="brand">Keelstone Prime<br>Automotive</div>
      <div class="divider"></div>
      <div class="contact">
        <h1 class="contact-name">Marlo Fenwicke</h1>
        <p class="contact-role">Director</p>
        <p class="contact-address">48 Tarn Lane<br>Whitianga 3510</p>
        <ul class="contact-lines">
          <li>
            <svg viewBox="0 0 16 16" aria-hidden="true"><path fill="#e41e26" d="M1 6c0-2 3-4 7-4s7 2 7 4v1h-3V5.5C11 5 9.5 4.8 8 4.8S5 5 4 5.5V7H1zM3.5 8.5 5 7h6l1.5 1.5V14h-9zM8 9.2a2 2 0 1 0 0 4 2 2 0 0 0 0-4z"/></svg>
            07 594 2713
          </li>
          <li>
            <svg viewBox="0 0 16 16" aria-hidden="true"><rect x="3.5" y="1" width="9" height="14" rx="1.5" fill="none" stroke="#e41e26" stroke-width="1.6"/><rect x="7" y="12" width="2" height="1.3" fill="#e41e26"/></svg>
            027 451 9362
          </li>
          <li>
            <svg viewBox="0 0 16 16" aria-hidden="true"><rect x="1" y="3" width="14" height="10" fill="#e41e26"/><path d="M1.5 3.5 8 9l6.5-5.5" fill="none" stroke="#fff" stroke-width="1.3"/></svg>
            office@keelstoneautomotive.example.nz
          </li>
        </ul>
      </div>
    </div>
    <div class="front-band">
      <span class="website">www.keelstoneautomotive.example.nz</span>
    </div>
  </section>

</body>
</html>
```